New website for a business that provides behaviour analysis

A new website that details the services that are provided around behaviour analysis for people with a disability through QPKV. There also needs to incorporate an about us and a staff page, Plus a referral form that is a google doc.
The business already has a web address that needs to be tailored.
Soft colours are preferred.
Do not have lots of pictures, keep them minimal.
A logo for the business is also needed to be incorporated, and this is a separate project that can be awarded to the website winner.
Website needs to be able to be used on WIX who will be the host for the design.

Target Market(s)

QPKV clients requiring behaviour support clician

Industry/Entity Type

Clinical behaviour support and analysis

Colors
00AB8E
00BBA5
67D7C9
C6EFE9
E9F9F6

Requirements
Must have
• Soft colours, preferable pale turquoise, minimal pictures, clean, sophisticated and classical look

```html
<!DOCTYPE html>
<html lang="en">
<head>
<meta charset="utf-8">
<title>QPKV Care – Contact</title>
<link href="https://fonts.googleapis.com/css2?family=Yeseva+One&family=Work+Sans:wght@400;500;600;700&display=swap" rel="stylesheet">
<style>
:root{
  --primary:#00AB8E;
  --accent:#00BBA5;
  --soft:#67D7C9;
  --pale:#C6EFE9;
  --mist:#E9F9F6;
  --page:#F8FCFC;
  --ink:#1F2B3D;
  --white:#FFFFFF;
  --map-a:#E7EBEC;
  --map-b:#DCE6EA;
}
*{margin:0;padding:0;box-sizing:border-box}
html,body{width:1200px;height:2285px;overflow:hidden}
body{position:relative;background:var(--white);font-family:"Work Sans",sans-serif;color:var(--ink)}
.abs{position:absolute}

/* top bar */
.brand{left:164px;top:18px;font-family:"Yeseva One",serif;font-size:31px;color:var(--primary);letter-spacing:.5px}
.info{top:18px;display:flex;gap:10px;align-items:center;color:var(--primary);font-size:13px;line-height:18px}
.info b{font-weight:500;display:block}
.info span{font-weight:500}

/* nav */
.nav{left:0;top:70px;width:1200px;height:70px;background:var(--primary)}
.nav ul{position:absolute;left:164px;top:26px;display:flex;gap:19px;list-style:none;color:var(--white);font-size:15.5px}
.nav li.active{font-weight:600}
.search{left:838px;top:24px}
.btn-appt{left:884px;top:15px;width:152px;height:40px;border-radius:20px;background:var(--mist);color:var(--primary);font-size:14px;font-weight:500;display:flex;align-items:center;justify-content:center}

/* hero */
.hero{left:0;top:140px;width:1200px;height:213px;background:linear-gradient(90deg,#E4EBEC 0%,#D6DFE2 50%,#CBD5D9 75%,#DDE4E6 100%)}
.hero-photo{left:560px;top:0;width:560px;height:213px;background:linear-gradient(90deg,rgba(214,223,226,0) 0%,#C2CCD1 40%,#BBC6CB 70%,rgba(221,228,230,0) 100%)}
.hero-blob1{left:-80px;top:-80px;width:185px;height:185px;border-radius:50%;background:#A8DCD3}
.hero-blob2{left:1088px;top:108px;width:180px;height:180px;border-radius:50%;background:#E2EDEC}
.crumb{left:164px;top:70px;color:var(--primary);font-size:15.5px}
.hero h1{position:absolute;left:164px;top:87px;font-family:"Yeseva One",serif;font-weight:400;font-size:43px;color:var(--primary)}
.stripe{top:353px;height:6px}

/* map */
.map{left:164px;top:417px;width:872px;height:394px;border-radius:4px;background:linear-gradient(135deg,var(--map-a) 0%,var(--map-b) 100%)}

/* contact */
.eyebrow{color:var(--primary);font-weight:700;font-size:15px;letter-spacing:3px}
.h2{font-family:"Yeseva One",serif;font-size:30px;color:var(--primary);font-weight:400}
.form{left:164px;top:954px;width:428px;height:341px}
.field{position:absolute;background:var(--primary);color:var(--white);font-size:14px;padding:14px 18px}
.submit{position:absolute;left:0;top:296px;width:428px;height:45px;background:var(--mist);color:var(--primary);font-size:14px;font-weight:500;display:flex;align-items:center;justify-content:center;letter-spacing:.5px}
.card{width:205px;height:205px;padding:44px 0 0 26px;background:var(--mist);color:var(--primary)}
.card.solid{background:var(--primary);color:var(--white)}
.card h3{font-size:16px;font-weight:700;margin:14px 0 6px;letter-spacing:.3px}
.card p{font-size:14.5px;line-height:24px}
.card p.small{font-size:13px}

/* news */
.news{left:0;top:1348px;width:1200px;height:561px;background:var(--page)}
.post{width:428px;height:135px;background:var(--white);box-shadow:0 2px 10px rgba(0,60,60,.06)}
.post .thumb{position:absolute;left:0;top:0;width:141px;height:135px;background:linear-gradient(135deg,#1B1C22 0%,#4A3A33 50%,#C7C9CF 100%)}
.post .meta{position:absolute;left:158px;top:18px;font-size:12px;color:var(--primary)}
.post .title{position:absolute;left:158px;top:40px;font-size:16px;line-height:22px;color:var(--ink)}
.post .stats{position:absolute;left:158px;top:104px;display:flex;gap:10px;font-size:12px;color:var(--ink);align-items:center}
.stats span{display:flex;gap:4px;align-items:center}
.dot{width:16px;height:16px;border-radius:50%;background:var(--mist)}

/* footer */
.footer{left:0;top:1909px;width:1200px;height:376px;background:var(--primary);color:var(--white)}
.footer .brand2{position:absolute;left:164px;top:60px;font-family:"Yeseva One",serif;font-size:31px}
.footer .tag{position:absolute;left:164px;top:108px;font-size:16px;line-height:22px}
.footer h4{position:absolute;top:51px;font-size:16px;font-weight:600}
.footer ul{position:absolute;top:108px;list-style:none;font-size:14.5px;line-height:26px}
.newsletter{left:796px;top:114px;width:239px;height:44px;background:var(--white);color:var(--primary);font-size:14px;padding:13px 9px}
.rule{left:164px;top:251px;width:872px;height:1px;background:rgba(255,255,255,.55)}
.copy{left:164px;top:292px;font-size:14.5px}
.social{top:292px;width:20px;height:20px;border-radius:50%;background:var(--white)}
</style>
</head>
<body>

<!-- top bar -->
<div class="abs brand">QPKV CARE</div>
<div class="abs info" style="left:490px">
  <svg width="32" height="32" viewBox="0 0 32 32" fill="none" stroke="#00AB8E" stroke-width="1.6"><path d="M9 5l4 6-3 3c1.5 3.5 4 6 7.5 7.5l3-3 6 4-2.5 4C14 26 6 18 5 8z"/><path d="M18 9a6 6 0 0 1 5 5M18 4a11 11 0 0 1 10 10"/></svg>
  <div><b>EMERGENCY</b><span>(214) 555-0137</span></div>
</div>
<div class="abs info" style="left:668px">
  <svg width="30" height="30" viewBox="0 0 30 30" fill="none" stroke="#00AB8E" stroke-width="1.6"><circle cx="15" cy="15" r="13"/><path d="M15 7v8l5 5"/></svg>
  <div><b>WORK HOUR</b><span>09:00 - 20:00 Everyday</span></div>
</div>
<div class="abs info" style="left:882px">
  <svg width="30" height="34" viewBox="0 0 30 34" fill="none" stroke="#00AB8E" stroke-width="1.6"><path d="M15 32S3 20 3 13a12 12 0 0 1 24 0c0 7-12 19-12 19z"/><circle cx="15" cy="13" r="4"/></svg>
  <div><b>LOCATION</b><span>48 Willow Lane</span></div>
</div>

<!-- nav -->
<div class="abs nav">
  <ul><li>Home</li><li>About us</li><li>Services</li><li>Doctors</li><li>News</li><li class="active">Contact</li></ul>
  <svg class="abs search" width="22" height="22" viewBox="0 0 22 22" fill="none" stroke="#fff" stroke-width="1.8"><circle cx="10" cy="10" r="8"/><path d="M16 16l4 4"/></svg>
  <div class="abs btn-appt">Appointment</div>
</div>

<!-- hero -->
<div class="abs hero" style="overflow:hidden">
  <div class="abs hero-photo" role="img" aria-label="Photo of a smiling doctor with a stethoscope in a clinic"></div>
  <div class="abs hero-blob1"></div>
  <div class="abs hero-blob2"></div>
  <div class="abs crumb">Home / Contact</div>
  <h1>Our Contacts</h1>
</div>
<div class="abs stripe" style="left:0;width:269px;background:var(--mist)"></div>
<div class="abs stripe" style="left:269px;width:736px;background:var(--primary)"></div>
<div class="abs stripe" style="left:1005px;width:195px;background:var(--accent)"></div>

<!-- map -->
<div class="abs map" role="img" aria-label="Street map showing the clinic location"></div>

<!-- get in touch -->
<div class="abs eyebrow" style="left:164px;top:869px">GET IN TOUCH</div>
<div class="abs h2" style="left:164px;top:890px">Contact</div>

<div class="abs form">
  <div class="field" style="left:0;top:0;width:213px;height:44px">Name</div>
  <div class="field" style="left:215px;top:0;width:213px;height:44px">Email</div>
  <div class="field" style="left:0;top:45px;width:428px;height:44px">Subject</div>
  <div class="field" style="left:0;top:90px;width:428px;height:206px">Message</div>
  <div class="submit">SUBMIT</div>
</div>

<div class="abs card" style="left:608px;top:868px">
  <svg width="32" height="32" viewBox="0 0 32 32" fill="none" stroke="#00AB8E" stroke-width="1.6"><path d="M9 5l4 6-3 3c1.5 3.5 4 6 7.5 7.5l3-3 6 4-2.5 4C14 26 6 18 5 8z"/><path d="M18 9a6 6 0 0 1 5 5M18 4a11 11 0 0 1 10 10"/></svg>
  <h3>EMERGENCY</h3><p>(214) 555-0137<br>(214) 555-0192</p>
</div>
<div class="abs card solid" style="left:831px;top:868px">
  <svg width="30" height="34" viewBox="0 0 30 34" fill="none" stroke="#fff" stroke-width="1.6"><path d="M15 32S3 20 3 13a12 12 0 0 1 24 0c0 7-12 19-12 19z"/></svg>
  <h3>LOCATION</h3><p>48 Willow Lane<br>Greenvale 4021</p>
</div>
<div class="abs card" style="left:608px;top:1090px">
  <svg width="34" height="30" viewBox="0 0 34 30" fill="none" stroke="#00AB8E" stroke-width="1.6"><rect x="1" y="3" width="32" height="24"/><path d="M1 3l16 13L33 3"/></svg>
  <h3>EMAIL</h3><p>hello@qpkvcare.org</p><p class="small">team@qpkvcare.org</p>
</div>
<div class="abs card" style="left:831px;top:1090px">
  <svg width="30" height="30" viewBox="0 0 30 30" fill="none" stroke="#00AB8E" stroke-width="1.6"><circle cx="15" cy="15" r="13"/><path d="M15 7v8l4 5"/></svg>
  <h3>WORKING HOURS</h3><p>Mon-Sat 09:00-20:00<br>Sunday Emergency only</p>
</div>

<!-- news -->
<div class="abs news">
  <div class="abs eyebrow" style="left:0;width:1200px;text-align:center;top:68px">BETTER INFORMATION, BETTER HEALTH</div>
  <div class="abs h2" style="left:0;width:1200px;text-align:center;top:88px">News</div>

  <div class="abs post" style="left:164px;top:174px">
    <div class="thumb" role="img" aria-label="Photo of a doctor examining a patient"></div>
    <div class="meta">Monday 05, September 2021 | By Author</div>
    <div class="title">This Article’s Title goes Here,<br>but not too long.</div>
    <div class="stats"><span><svg width="16" height="10" viewBox="0 0 16 10" fill="none" stroke="#4A63D8" stroke-width="1.3"><path d="M1 5s3-4 7-4 7 4 7 4-3 4-7 4-7-4-7-4z"/><circle cx="8" cy="5" r="2"/></svg>68</span><span><svg width="14" height="12" viewBox="0 0 14 12" fill="none" stroke="#E0364C" stroke-width="1.4"><path d="M7 11S1 7 1 4a3 3 0 0 1 6-1 3 3 0 0 1 6 1c0 3-6 7-6 7z"/></svg>86</span></div>
  </div>
  <div class="abs post" style="left:608px;top:174px">
    <div class="thumb" role="img" aria-label="Photo of a doctor examining a patient"></div>
    <div class="meta">Monday 05, September 2021 | By Author</div>
    <div class="title">This Article’s Title goes Here,<br>but not too long.</div>
    <div class="stats"><span><svg width="16" height="10" viewBox="0 0 16 10" fill="none" stroke="#4A63D8" stroke-width="1.3"><path d="M1 5s3-4 7-4 7 4 7 4-3 4-7 4-7-4-7-4z"/><circle cx="8" cy="5" r="2"/></svg>68</span><span><svg width="14" height="12" viewBox="0 0 14 12" fill="none" stroke="#E0364C" stroke-width="1.4"><path d="M7 11S1 7 1 4a3 3 0 0 1 6-1 3 3 0 0 1 6 1c0 3-6 7-6 7z"/></svg>86</span></div>
  </div>
  <div class="abs post" style="left:164px;top:327px">
    <div class="thumb" role="img" aria-label="Photo of a doctor examining a patient"></div>
    <div class="meta">Monday 05, September 2021 | By Author</div>
    <div class="title">This Article’s Title goes Here,<br>but not too long.</div>
    <div class="stats"><span><svg width="16" height="10" viewBox="0 0 16 10" fill="none" stroke="#4A63D8" stroke-width="1.3"><path d="M1 5s3-4 7-4 7 4 7 4-3 4-7 4-7-4-7-4z"/><circle cx="8" cy="5" r="2"/></svg>68</span><span><svg width="14" height="12" viewBox="0 0 14 12" fill="none" stroke="#E0364C" stroke-width="1.4"><path d="M7 11S1 7 1 4a3 3 0 0 1 6-1 3 3 0 0 1 6 1c0 3-6 7-6 7z"/></svg>86</span></div>
  </div>
  <div class="abs post" style="left:608px;top:327px">
    <div class="thumb" role="img" aria-label="Photo of a doctor examining a patient"></div>
    <div class="meta">Monday 05, September 2021 | By Author</div>
    <div class="title">This Article’s Title goes Here,<br>but not too long.</div>
    <div class="stats"><span><svg width="16" height="10" viewBox="0 0 16 10" fill="none" stroke="#4A63D8" stroke-width="1.3"><path d="M1 5s3-4 7-4 7 4 7 4-3 4-7 4-7-4-7-4z"/><circle cx="8" cy="5" r="2"/></svg>68</span><span><svg width="14" height="12" viewBox="0 0 14 12" fill="none" stroke="#E0364C" stroke-width="1.4"><path d="M7 11S1 7 1 4a3 3 0 0 1 6-1 3 3 0 0 1 6 1c0 3-6 7-6 7z"/></svg>86</span></div>
  </div>

  <div class="abs dot" style="left:567px;top:490px"></div>
  <div class="abs dot" style="left:592px;top:490px;background:var(--primary)"></div>
  <div class="abs dot" style="left:617px;top:490px"></div>
</div>

<!-- footer -->
<div class="abs footer">
  <div class="brand2">QPKV CARE</div>
  <div class="tag">Leading the Way in Medical<br>Execellence, Trusted Care.</div>
  <h4 style="left:406px">Important Links</h4>
  <ul style="left:406px"><li>Appointment</li><li>Doctors</li><li>Services</li><li>About Us</li></ul>
  <h4 style="left:560px">Contact Us</h4>
  <ul style="left:560px"><li>Call: (214) 555-0137</li><li>Email: hello@qpkvcare.org</li><li>Address: 48 Willow Lane</li><li>Greenvale 4021</li></ul>
  <h4 style="left:796px">Newsletter</h4>
  <div class="abs newsletter">Enter your email address
    <svg class="abs" style="right:16px;top:12px" width="22" height="20" viewBox="0 0 22 20" fill="#1F2B6D"><path d="M21 1L1 9l7 3 2 7 3-5 5 3z"/></svg>
  </div>
  <div class="abs rule"></div>
  <div class="abs copy">© 2021 QPKV Care All Rights Reserved by Ferncroft Studio</div>
  <div class="abs social" style="left:938px"></div>
  <div class="abs social" style="left:977px"></div>
  <div class="abs social" style="left:1016px"></div>
</div>

</body>
</html>
```